Zenqo - revolutionary mobile payment

The app is a P2P money trasfert, without the using of credit card or bank circuits it can transfer electronic money from one person to another consumers simply and immediatelly.
You can use the color you want, but the message we need to transert to consumer is simplicity, safety and coolness.
In attach the logo of the company and the wireframe of thre page of the app.
The goal is to design the page of the app with a clear, simple and intuitive graphic.
Updates

I have upgrade the brief with important information and detail, many thanks

Target Market(s)

all the people

Industry/Entity Type

Credit Card

Requirements
Must have
• You have to design one icon for each button in the first page, (shop is: where to shop)
in the second one a new intuitive image (instead of the hand) that let the user to understand that with a simple swipe he can process the payment
Nice to have
• You can include or esxclude what you want or belive can improve user experience of the app
Should not have
• too much color, too much button or information

```html
<!DOCTYPE html>
<html lang="it">
<head>
<meta charset="utf-8">
<title>Zenqo – Pay</title>
<link rel="stylesheet" href="https://fonts.googleapis.com/css2?family=Questrial&family=Nunito:wght@600;700;800&display=swap">
<style>
  :root {
    --page-bg: #eeeff1;
    --status-bg: #0b0b0d;
    --header-top: #f4f4f5;
    --header-bottom: #d9d9dc;
    --band-left: #3f4f77;
    --band-right: #5a6f9e;
    --back-bg: #2f4170;
    --brand-blue: #1f3a78;
    --key-blue: #2e4677;
    --key-blue-dark: #263b69;
    --key-line: #6d7ea4;
    --key-accent: #e45200;
    --field-bg: #dedde2;
    --amount-bg: #8d8d93;
    --ink: #111114;
    --white: #ffffff;
  }
  html, body {
    margin: 0;
    width: 768px;
    height: 1200px;
    overflow: hidden;
    background: var(--page-bg);
    font-family: "Questrial", sans-serif;
  }
  .screen {
    position: absolute;
    left: 49px;
    top: 0;
    width: 670px;
    height: 1200px;
    overflow: hidden;
    background: #b9b8bf;
  }
  .status-bar {
    position: absolute; left: 0; top: 0; width: 100%; height: 53px;
    background: var(--status-bg); color: var(--white);
    font-family: "Nunito", sans-serif; font-weight: 600; font-size: 22px;
    display: flex; align-items: center; justify-content: space-between;
    padding: 0 18px; box-sizing: border-box;
  }
  .status-left, .status-right { display: flex; align-items: center; gap: 8px; width: 200px; }
  .status-right { justify-content: flex-end; }
  .app-header {
    position: absolute; left: 0; top: 53px; width: 100%; height: 80px;
    background: linear-gradient(var(--header-top), var(--header-bottom));
  }
  .settings-icon { position: absolute; left: 16px; top: 16px; }
  .brand {
    position: absolute; right: 20px; top: 21px;
    display: flex; align-items: center; gap: 8px;
    color: var(--brand-blue); font-family: "Nunito", sans-serif; font-size: 30px; font-weight: 800;
  }
  .brand-dot { width: 34px; height: 34px; border-radius: 50%; background: var(--brand-blue); }
  .title-band {
    position: absolute; left: 0; top: 133px; width: 100%; height: 146px;
    background: linear-gradient(90deg, var(--band-left), var(--band-right));
  }
  .back-button {
    position: absolute; left: 0; top: 0; width: 133px; height: 146px;
    background: var(--back-bg); color: var(--white);
    display: flex; align-items: center; padding-left: 10px; box-sizing: border-box;
    font-size: 25px; white-space: nowrap;
  }
  .screen-title {
    position: absolute; left: 133px; right: 0; top: 0; height: 146px; margin: 0;
    display: flex; align-items: center; justify-content: center; gap: 14px;
    color: var(--white); font-family: "Nunito", sans-serif; font-weight: 700; font-size: 50px;
  }
  .swipe-icon {
    width: 66px; height: 62px; border-radius: 8px;
    background: linear-gradient(135deg, rgba(255,255,255,.85), rgba(255,255,255,.45));
  }
  .backdrop {
    position: absolute; left: 0; top: 279px; width: 100%; height: 921px;
    background:
      radial-gradient(ellipse 260px 200px at 40% 20%, rgba(160,130,140,.55), transparent),
      radial-gradient(ellipse 200px 180px at 60% 45%, rgba(70,120,170,.6), transparent),
      radial-gradient(ellipse 220px 260px at 90% 30%, rgba(220,225,235,.8), transparent),
      linear-gradient(180deg, #b7b4ba, #c9c8ce 50%, #a8adc0);
  }
  .phone-field {
    position: absolute; left: 102px; top: 352px; width: 494px; height: 78px;
    background: var(--field-bg); border: 1px solid #a9a9ae; box-sizing: border-box;
    display: flex; align-items: center;
  }
  .phone-field-icon {
    width: 62px; height: 100%; background: var(--white); border-right: 1px solid #a9a9ae;
    display: flex; align-items: center; justify-content: center;
  }
  .phone-field-text { padding-left: 12px; font-size: 28px; color: var(--ink); }
  .phone-field-text b { font-family: "Nunito", sans-serif; font-weight: 700; margin-right: 12px; }
  .currency {
    position: absolute; left: 40px; top: 500px;
    font-family: "Nunito", sans-serif; font-weight: 800; font-size: 70px; color: var(--ink); line-height: 1;
  }
  .amount {
    position: absolute; left: 102px; top: 484px; width: 494px; height: 117px;
    background: linear-gradient(90deg, #a3a3a8, var(--amount-bg));
    display: flex; align-items: center; justify-content: center;
    font-family: "Nunito", sans-serif; font-size: 70px; font-weight: 800;
    color: var(--ink); letter-spacing: 3px;
  }
  .notes-toggle {
    position: absolute; left: 14px; top: 647px; width: 255px; height: 37px;
    background: rgba(110,125,165,.8); color: var(--white);
    font-size: 17px; display: flex; align-items: center; padding-left: 10px; box-sizing: border-box; gap: 12px;
    white-space: nowrap;
  }
  .keypad {
    position: absolute; left: 14px; top: 692px; width: 639px; height: 490px;
    display: grid; grid-template-columns: repeat(3, 1fr); grid-template-rows: repeat(4, 1fr); gap: 5px;
  }
  .key {
    background: linear-gradient(135deg, var(--key-blue), var(--key-blue-dark));
    box-shadow: inset 0 -2px 0 var(--key-line);
    color: var(--white); font-family: "Nunito", sans-serif; font-weight: 700; font-size: 54px;
    display: flex; align-items: center; justify-content: center;
  }
  .key--active { background: var(--key-accent); }
</style>
</head>
<body>
<main class="screen">
  <div class="status-bar">
    <div class="status-left">●●●○○ VOLT
      <svg width="24" height="18" viewBox="0 0 24 18"><path d="M2 6a14 14 0 0 1 20 0M6 10a8 8 0 0 1 12 0M12 16l-3-3a4 4 0 0 1 6 0z" fill="none" stroke="#fff" stroke-width="2.5"/></svg>
    </div>
    <div class="status-time">4:21 PM</div>
    <div class="status-right">
      <svg width="12" height="22" viewBox="0 0 12 22"><path d="M1 6l10 10-5 5V1l5 5L1 16" fill="none" stroke="#888" stroke-width="1.6"/></svg>
      22%
      <svg width="50" height="22" viewBox="0 0 50 22"><rect x="1" y="2" width="44" height="18" rx="3" fill="none" stroke="#fff" stroke-width="2"/><rect x="4" y="5" width="9" height="12" fill="#fff"/><rect x="46" y="8" width="3" height="6" fill="#fff"/></svg>
    </div>
  </div>

  <header class="app-header">
    <svg class="settings-icon" width="48" height="48" viewBox="0 0 48 48" aria-label="Impostazioni">
      <g fill="#2b2b2f">
        <circle cx="18" cy="30" r="11"/>
        <g stroke="#2b2b2f" stroke-width="5"><path d="M18 14v32M2 30h32M7 19l22 22M29 19L7 41"/></g>
        <circle cx="36" cy="13" r="7"/>
        <g stroke="#2b2b2f" stroke-width="3.5"><path d="M36 2v22M25 13h22M28 5l16 16M44 5L28 21"/></g>
      </g>
      <circle cx="18" cy="30" r="4" fill="#e4e4e6"/><circle cx="36" cy="13" r="2.5" fill="#e4e4e6"/>
    </svg>
    <div class="brand"><span class="brand-dot"></span>Zenqo</div>
  </header>

  <section class="title-band">
    <div class="back-button">‹ Indietro</div>
    <h1 class="screen-title">
      <span class="swipe-icon" role="img" aria-label="Icona di pagamento con scorrimento"></span>
      Pay
    </h1>
  </section>

  <div class="backdrop" role="img" aria-label="Sfondo fotografico sfocato in toni grigio, rosa e blu"></div>

  <div class="phone-field">
    <div class="phone-field-icon">
      <svg width="30" height="48" viewBox="0 0 30 48"><rect x="2" y="2" width="26" height="44" rx="4" fill="none" stroke="#111" stroke-width="3"/><rect x="6" y="8" width="18" height="30" fill="#111"/><circle cx="15" cy="42" r="2" fill="#111"/></svg>
    </div>
    <div class="phone-field-text"><b>+39</b>Cellulare</div>
  </div>

  <div class="currency">€</div>
  <div class="amount">851.33</div>

  <div class="notes-toggle">Inserisci note (opzionale) <span>▼</span></div>

  <div class="keypad">
    <div class="key">1</div><div class="key">2</div><div class="key">3</div>
    <div class="key">4</div><div class="key">5</div><div class="key">6</div>
    <div class="key">7</div><div class="key key--active">8</div><div class="key">9</div>
    <div class="key">.</div><div class="key">0</div>
    <div class="key" aria-label="Cancella">
      <svg width="66" height="40" viewBox="0 0 66 40"><path d="M16 2h48v36H16L2 20z" fill="#fff"/><path d="M30 12l16 16M46 12L30 28" stroke="#2e4677" stroke-width="5"/></svg>
    </div>
  </div>
</main>
</body>
</html>
```